KRT Flyer to attract applicants 11x17

Lantern Stagehand Collective provides crew for local concerts, filming, theater, and corporate events.
The flyer will be posted on bulletin boards at colleges with theater programs.
Our primary venues are historic theaters in downtown LA
Need a 11x17 poster to attract potential applicants/crew
I have attached a poster that one of our staff made that has all if the relevant info - but i know the poster can look much better than that. I have also attached many images and our logo. It is not necessary to use all of the images, or any of them. The two images of the theater interiors are the venues we operate so they would be the first to include. I can send additional info or images upon request. Thank you

Industry/Entity Type

Entertainment

Requirements
Must have
• APPLY@KRTCREW.EXAMPLE

```html
<!DOCTYPE html>
<html lang="en">
<head>
<meta charset="utf-8">
<title>KRT – Open Positions</title>
<link rel="stylesheet" href="https://fonts.googleapis.com/css2?family=Montserrat:wght@300;400;700;800;900&display=swap">
<style>
  :root {
    --ink: #060608;
    --paper: #ffffff;
    --brand-blue: #1f5aa6;
    --gold: #c98a2a;
    --crimson: #9c1b1b;
    --steel: #2a2c31;
    --violet: #4b3fb0;
    --plum: #3a1d4a;
  }
  * { margin: 0; padding: 0; box-sizing: border-box; }
  html, body { width: 777px; height: 1200px; overflow: hidden; background: var(--ink); }
  .poster {
    position: relative;
    width: 777px;
    height: 1200px;
    background: var(--ink);
    font-family: "Montserrat", sans-serif;
    color: var(--paper);
    overflow: hidden;
  }
  .photo { position: absolute; }
  .photo--theater-gold {
    left: 50px; top: 45px; width: 335px; height: 282px;
    background: linear-gradient(100deg, #7a4a12 0%, var(--gold) 35%, #a4601c 60%, var(--crimson) 85%, #3a0a0a 100%);
  }
  .photo--console {
    left: 395px; top: 48px; width: 330px; height: 279px;
    background: linear-gradient(160deg, #0b0c10 0%, #1b1d24 30%, var(--steel) 60%, #5a5d64 85%, #1a1b1f 100%);
  }
  .photo--spotlight {
    left: 50px; top: 327px; width: 335px; height: 282px;
    background: radial-gradient(ellipse at 25% 70%, #c9d4ff 0%, #7a7ce0 22%, var(--violet) 50%, #2a2170 100%);
  }
  .photo--theater-ornate {
    left: 385px; top: 327px; width: 341px; height: 268px;
    background: radial-gradient(ellipse at 50% 35%, #d9a25a 0%, #9a4a3a 30%, var(--plum) 65%, #1a0e22 100%);
  }
  .brand-mark {
    position: absolute;
    left: 394px; top: 310px;
    transform: translate(-50%, -50%);
    font-weight: 800;
    font-size: 64px;
    letter-spacing: 2px;
    color: var(--paper);
    line-height: 1;
  }
  .headline {
    position: absolute;
    left: 51px; top: 562px;
    font-weight: 800;
    font-size: 95px;
    line-height: 88px;
    letter-spacing: -1px;
    white-space: nowrap;
  }
  .intro {
    position: absolute;
    left: 55px; top: 744px;
    font-weight: 400;
    font-size: 33px;
    line-height: 43px;
    white-space: nowrap;
  }
  .divider {
    position: absolute;
    left: 56px; top: 942px;
    width: 79px; height: 4px;
    background: var(--brand-blue);
  }
  .apply-label {
    position: absolute;
    left: 55px; top: 970px;
    font-weight: 400;
    font-size: 33px;
    line-height: 1;
    white-space: nowrap;
  }
  .apply-pill {
    position: absolute;
    left: 55px; top: 1013px;
    width: 400px; height: 60px;
    background: var(--brand-blue);
    border-radius: 0 30px 30px 0;
    display: flex; align-items: center;
    padding-left: 26px;
    font-weight: 800;
    font-size: 21px;
    letter-spacing: 0.2px;
    white-space: nowrap;
  }
  .footer {
    position: absolute;
    left: 0; top: 1122px;
    width: 777px; height: 78px;
    background: var(--paper);
  }
  .footer__url {
    position: absolute;
    right: 48px; top: 23px;
    font-weight: 900;
    font-size: 22px;
    color: var(--ink);
    line-height: 1;
    white-space: nowrap;
  }
</style>
</head>
<body>
  <main class="poster">
    <div class="photo photo--theater-gold" role="img" aria-label="Gilded historic theater interior with balconies and red stage curtain"></div>
    <div class="photo photo--console" role="img" aria-label="Lighting control console with touch screens and faders"></div>
    <div class="photo photo--spotlight" role="img" aria-label="Follow spotlight hanging on chains beaming blue-violet light"></div>
    <div class="photo photo--theater-ornate" role="img" aria-label="Ornate historic theater auditorium with domed ceiling and stage"></div>

    <div class="brand-mark">KRT</div>

    <h1 class="headline">OPEN<br>POSITIONS!</h1>

    <p class="intro">WE ARE LOOKING FOR<br>TALENTED TECHNICIANS TO ADD<br>TO OUR ROSTER OF SKILLED<br>PROFESSIONALS.</p>

    <div class="divider"></div>

    <p class="apply-label">SEND RESUME TO</p>
    <div class="apply-pill">APPLY@KRTCREW.EXAMPLE</div>

    <footer class="footer">
      <span class="footer__url">WWW.KRTCREW.EXAMPLE</span>
    </footer>
  </main>
</body>
</html>
```